Packaging design for a reclosable bag for our product

We have a logo, and we need to put it on packaging for our product and while we want the look to be simple, we want it to follow good design principles and also contain spaces for other product descriptions.

There will be 5 sizes at launch so I'd like 5 variations, one for each size.

I've included a few mockups of the type of bag that I made but they are all just rough ideas that I had.

I want the brand to look scientific and methodical and even a bit quirky, as in "wow this is a serious product but also a bit unusual."

```html
<!DOCTYPE html>
<html lang="en">
<head>
<meta charset="UTF-8">
<title>KVELD Bias Lighting – Extra Large Pack</title>
<link rel="stylesheet" href="https://fonts.googleapis.com/css2?family=Roboto:wght@300&display=swap">
<style>
  :root {
    --bg: #000000;
    --ink: #ffffff;
    --edge: #555555;
  }
  html, body {
    margin: 0;
    padding: 0;
    width: 960px;
    height: 1200px;
    overflow: hidden;
    background: var(--bg);
  }
  .pack {
    position: relative;
    width: 960px;
    height: 1200px;
    background: var(--bg);
    box-shadow: inset 0 0 0 1px var(--edge);
    font-family: "Roboto", Arial, sans-serif;
    font-weight: 300;
    color: var(--ink);
    overflow: hidden;
  }
  .graphics {
    position: absolute;
    inset: 0;
  }
  .line {
    position: absolute;
    left: 0;
    width: 960px;
    margin: 0;
    text-align: center;
    line-height: 1;
    white-space: nowrap;
    font-weight: 300;
  }
  .size-name    { top: 173px; font-size: 58px; }
  .size-length  { top: 252px; font-size: 68px; }
  .brand-name   { top: 546px; font-size: 112px; letter-spacing: 4px; }
  .product-name { top: 810px; font-size: 92px; }
  .spec {
    top: 982px;
    font-size: 38px;
    line-height: 47px;
  }
</style>
</head>
<body>
  <main class="pack">
    <svg class="graphics" width="960" height="1200" viewBox="0 0 960 1200" aria-hidden="true">
      <polygon class="notch-top" points="424.6,0 567.6,0 495.8,86.3" fill="var(--ink)"/>
      <polygon class="notch-bottom" points="424.6,1200 567.6,1200 495.8,1114" fill="var(--ink)"/>
    </svg>

    <p class="line size-name">Extra Large</p>
    <p class="line size-length">5 meters</p>
    <h1 class="line brand-name">KVELD</h1>
    <h2 class="line product-name">Bias Lighting</h2>
    <p class="line spec">Simulated D65 CRI 90+<br>6500K White Bias Lighting</p>
  </main>
</body>
</html>
```